Computer Training in the Education sector - Letterhead

We need a new letter head to be designed for the company. We provide computer training fro the Education Sector, both primary and private tertiary providers. The colours will need to tie in with the website www.crossingthestream.co.nz.
The company name is Crossing the Stream with the tag line of Computer Training for Educators.
The footer will need to have the following detail...
0508 PCS MENTOR
021 839 415
www.crossingthestream.co.nz / training@crossingthestream.co.nz
Updates

Thanks for the designs so far.

Some have watermarks in the background. Please don't worry about using watermarks as I will not be using a watermark in in a final design.
Regards,
Roger

Thank you for all the designs and the effort. There was some great concepts that came through.

Cheers
Roger

Industry/Entity Type

Computer

```html
<!DOCTYPE html>
<html lang="en">
<head>
<meta charset="utf-8">
<title>Crossing the Stream – Letterhead</title>
<link rel="stylesheet" href="https://fonts.googleapis.com/css2?family=Jost:wght@300;400;700&family=Quicksand:wght@500&display=swap">
<style>
  :root {
    --paper: #ffffff;
    --ink: #1c1c1c;
    --ink-soft: #3a3a3a;
    --rule: #555555;
    --brand-blue: #2f74b8;
    --brand-green: #86bc3f;
  }
  html, body {
    margin: 0;
    padding: 0;
    width: 1034px;
    height: 1200px;
    overflow: hidden;
    background: var(--paper);
  }
  .letterhead {
    position: relative;
    width: 1034px;
    height: 1200px;
    background: var(--paper);
    font-family: "Jost", "Futura", sans-serif;
  }
  .brand {
    position: absolute;
    left: 48px;
    top: 58px;
    margin: 0;
    font-family: "Quicksand", sans-serif;
    font-weight: 500;
    font-size: 34px;
    line-height: 1.05;
    color: var(--brand-blue);
  }
  .contact {
    position: absolute;
    left: 700px;
    top: 60px;
    height: 84px;
    padding-left: 20px;
    border-left: 1px solid var(--rule);
    list-style: none;
    margin: 0;
    font-weight: 300;
    font-size: 17px;
    color: var(--ink-soft);
  }
  .contact li {
    display: flex;
    align-items: center;
    gap: 6px;
    height: 22px;
    line-height: 22px;
  }
  .contact svg {
    width: 13px;
    height: 13px;
    flex: none;
  }
  .tagline {
    position: absolute;
    left: 0;
    right: 0;
    top: 1140px;
    margin: 0;
    text-align: center;
    font-weight: 700;
    font-size: 22px;
    letter-spacing: 2.4px;
    color: var(--ink);
  }
  .footer-bands {
    position: absolute;
    left: 0;
    bottom: 0;
    width: 1034px;
    height: 26px;
  }
</style>
</head>
<body>
<main class="letterhead">
  <h1 class="brand">Crossing the<br>Stream</h1>

  <ul class="contact">
    <li>
      <svg viewBox="0 0 16 16" aria-hidden="true"><circle cx="8" cy="8" r="7" fill="none" stroke="#333" stroke-width="1.4"/><path d="M5.5 4.5l1.5 1.5-1 1c.6 1.3 1.6 2.3 2.9 2.9l1-1 1.6 1.5-1.3 1.2c-2.6-.6-4.9-2.9-5.6-5.6z" fill="#333"/></svg>
      0508 PCS MENTOR
    </li>
    <li>
      <svg viewBox="0 0 16 16" aria-hidden="true"><circle cx="8" cy="8" r="7" fill="none" stroke="#333" stroke-width="1.4"/><path d="M5.5 4.5l1.5 1.5-1 1c.6 1.3 1.6 2.3 2.9 2.9l1-1 1.6 1.5-1.3 1.2c-2.6-.6-4.9-2.9-5.6-5.6z" fill="#333"/></svg>
      021 839 415
    </li>
    <li>
      <svg viewBox="0 0 16 16" aria-hidden="true"><path d="M1.5 6.5L8 2.5l6.5 4v7h-13z" fill="#333"/><path d="M2.5 7l5.5 3.5L13.5 7" fill="none" stroke="#fff" stroke-width="1.2"/></svg>
      training@crossingthestream.co.nz
    </li>
    <li>
      <svg viewBox="0 0 16 16" aria-hidden="true"><g fill="none" stroke="#333" stroke-width="1.2"><circle cx="8" cy="8" r="6.5"/><ellipse cx="8" cy="8" rx="3" ry="6.5"/><path d="M1.5 8h13M2.5 4.8h11M2.5 11.2h11"/></g></svg>
      www.crossingthestream.co.nz
    </li>
  </ul>

  <p class="tagline">Computer Training for Educators</p>

  <svg class="footer-bands" viewBox="0 1174 1034 26" aria-hidden="true">
    <polygon points="0,1178 490,1178 444,1200 0,1200" fill="var(--brand-green)"/>
    <polygon points="500,1178 1034,1175 1034,1200 460,1200" fill="var(--brand-blue)"/>
  </svg>
</main>
</body>
</html>
```